Flyer for Medical practice welcoming new patients

We need a DL size brochure designed for Medical practice to advertise that we are accepting new patients. Our practice has special interests in women's and children's health and seniors health. Our existing advertising materials are in the colour scheme of purples I have uploaded our logo which includes our colour scheme.

Target Market(s)

Versatile to target anyone looking for a small medical practice that offers continuous care of seeing the same Doctor every time

Industry/Entity Type

Advertising

Font styles to use
Serif

Colors
6b449b
876aae
b7a5cc

Requirements
Must have
• The practice logo of just the picture not Dr Petra Holcombe.
• Purple colour scheme.
• Practice name: Tarrabeen Medical Practice.
• Address: 147 Corlett Rd, Tarrabeen NSW 2500.
• Phone: 4871 6035.
• DL size brochure
• Welcoming new patients ( a strong emphasis needs to be placed on this)
• Nurse and onsite ECG's and lung function tests.
• Travel vaccines including yellow fever
• Bulk billing for tertiary students
• We would also like design to alter the text so that we can change the points to be reflect who we are targeting at the time.
Nice to have
• The practice logo with Dr Petra Holcombe somewhere not as a feature as the practice no longer goes under this name but is still well known as Dr Holcombe's.

```html
<!DOCTYPE html>
<html lang="en">
<head>
<meta charset="utf-8">
<title>Tarrabeen Medical Practice – DL Flyer</title>
<link rel="stylesheet" href="https://fonts.googleapis.com/css2?family=Carlito:wght@400;700&family=PT+Sans+Narrow:wght@700&family=Mulish:wght@700&display=swap">
<style>
  :root {
    --purple-deep: #6b449b;
    --purple-mid: #876aae;
    --purple-light: #b7a5cc;
    --purple-text: #5b3a91;
    --lavender-name: #e6dcf1;
    --white: #ffffff;
    --backdrop: #e4e4e6;
  }
  * { margin: 0; padding: 0; box-sizing: border-box; }
  html, body {
    width: 1200px; height: 1000px; overflow: hidden;
    background: var(--backdrop);
  }
  .flyer {
    position: absolute; left: 346px; top: 30px;
    width: 440px; height: 925px;
    background: var(--white);
    overflow: hidden;
  }
  .flyer-shapes { position: absolute; inset: 0; }
  .brand {
    position: absolute; left: 12px; top: 76px;
    display: flex; align-items: center; gap: 40px;
  }
  .brand-mark {
    width: 110px; height: 110px; border-radius: 50%;
    border: 4px solid var(--lavender-name);
    flex: none;
  }
  .brand-name {
    font-family: "Carlito", "Calibri", sans-serif;
    font-weight: 400; font-size: 29px; line-height: 32px;
    color: var(--lavender-name);
  }
  .headline {
    position: absolute; left: 0; width: 442px; top: 304px;
    text-align: center; color: var(--white);
    font-family: "PT Sans Narrow", "Arial Narrow", sans-serif;
    font-weight: 700; text-shadow: 1px 2px 2px rgba(40, 20, 70, .6);
  }
  .headline-lead { display: block; font-size: 21px; line-height: 22px; }
  .headline-main { display: block; font-size: 33px; line-height: 34px; letter-spacing: .2px; }
  .services {
    position: absolute; left: 8px; top: 437px; width: 430px;
    list-style: none;
    font-family: "Carlito", "Calibri", sans-serif;
    font-size: 21px; line-height: 26px; color: var(--purple-text);
  }
  .services li { position: relative; padding-left: 14px; margin-bottom: 38px; }
  .services li::before {
    content: ""; position: absolute; left: 0; top: 8px;
    width: 10px; height: 10px; border-radius: 50%;
    background: var(--purple-deep);
  }
  .contact {
    position: absolute; left: 7px; bottom: 10px;
    font-family: "Mulish", "Century Gothic", sans-serif;
    font-weight: 700; color: var(--white);
  }
  .contact-title { font-size: 13px; letter-spacing: .6px; margin-bottom: 10px; }
  .contact-line { font-size: 15px; line-height: 24px; letter-spacing: .3px; }
</style>
</head>
<body>
  <main class="flyer">
    <svg class="flyer-shapes" width="440" height="925" viewBox="0 0 440 925" aria-hidden="true">
      <defs>
        <linearGradient id="header-fill" x1="0" y1="0" x2="0" y2="1">
          <stop offset="0" stop-color="#7d5cab"/>
          <stop offset="1" stop-color="#6a439a"/>
        </linearGradient>
        <linearGradient id="wave-light-fill" x1="1" y1="0" x2="0" y2="1">
          <stop offset="0" stop-color="#a994cc"/>
          <stop offset="1" stop-color="#8a6db3"/>
        </linearGradient>
        <linearGradient id="footer-fill" x1="0" y1="0" x2="0" y2="1">
          <stop offset="0" stop-color="#8a6cb2"/>
          <stop offset="1" stop-color="#6b449b"/>
        </linearGradient>
        <filter id="soft-shadow" x="-10%" y="-10%" width="120%" height="130%">
          <feDropShadow dx="0" dy="6" stdDeviation="6" flood-color="#3c2060" flood-opacity=".35"/>
        </filter>
      </defs>
      <!-- header panel -->
      <path class="header-panel" d="M0,0 H440 V125 C390,200 290,262 190,262 C110,262 50,248 0,230 Z" fill="url(#header-fill)" filter="url(#soft-shadow)"/>
      <ellipse class="header-arc" cx="148" cy="-22" rx="168" ry="86" fill="var(--purple-light)"/>
      <!-- headline oval -->
      <ellipse class="headline-oval" cx="221" cy="343" rx="215" ry="45" fill="var(--purple-deep)"/>
      <!-- lower waves -->
      <path class="wave-light" d="M440,505 C360,540 300,620 200,680 C120,725 50,742 0,748 V925 H440 Z" fill="url(#wave-light-fill)" filter="url(#soft-shadow)"/>
      <path class="wave-band" d="M440,598 C350,650 250,715 120,738 C70,746 30,748 0,748 V925 H440 Z" fill="#7a55a8" filter="url(#soft-shadow)"/>
      <path class="wave-gap" d="M440,660 C340,715 200,742 0,762 V925 H440 Z" fill="#f7f4fa" filter="url(#soft-shadow)"/>
      <path class="footer-panel" d="M440,708 C330,758 150,768 0,775 V925 H440 Z" fill="url(#footer-fill)" filter="url(#soft-shadow)"/>
    </svg>

    <header class="brand">
      <span class="brand-mark"></span>
      <h1 class="brand-name">Tarrabeen<br>Medical Practice</h1>
    </header>

    <h2 class="headline">
      <span class="headline-lead">WE ARE NOW</span>
      <span class="headline-main">ACCEPTING NEW PATIENTS!</span>
    </h2>

    <ul class="services">
      <li>Nurse on site for ECG's, lung function tests, health assessments and much more</li>
      <li>We offer travel vaccines including<br>&nbsp;yellow fever</li>
      <li>Bulk billing for tertiary<br>students</li>
    </ul>

    <footer class="contact">
      <p class="contact-title">CONTACT DETAILS:</p>
      <p class="contact-line">Address: 147 Corlett Rd, Tarrabeen NSW 2500</p>
      <p class="contact-line">Telephone: 4871 6035</p>
    </footer>
  </main>
</body>
</html>
```